Website to design and sell sundials: www.gnomonvale.com

We have a website that creates a free paper sundial, we want to migrate from this not profit free website to a website where we will continue offering the free paper sundial model but We will also offer a manufactured sundial and sell it.
In order to understand the project, please visit:
http://www.gnomonvale.com/vertical/sundial.html and
http://www.torvel.net/landing/

The website user journey should be redesigned, including the phases that are,
select language
Show product give info
Creation/edit sundial (could be one or more phases)
View created sundial
Buy sundial.

May some of them could be combined or splitted, what It have more sense.

Requirements
Must have
• A description page user journey offering freemium paper sundial and physical sundial to sell.
• A sundial creation page for "free" paper sundial
• A result page for paper sundial
• A sell page for physical

```html
<!DOCTYPE html>
<html lang="en">
<head>
<meta charset="utf-8">
<title>GnomonVale – Product Page</title>
<link href="https://fonts.googleapis.com/css2?family=Roboto:wght@300;400;500;700&display=swap" rel="stylesheet">
<style>
:root{
  --red:#b71c1c;
  --red-bright:#c3302b;
  --footer-red:#c33633;
  --orange-top:#f6b83b;
  --orange-bottom:#e59510;
  --dark:#333333;
  --black:#1b1b1b;
  --grey-bg:#eeeeee;
  --row-alt:#efefef;
  --text:#444444;
  --photo-light:#e6e6e6;
  --photo-dark:#c9c9c9;
  --white:#ffffff;
}
*{box-sizing:border-box;margin:0;padding:0}
html,body{width:1200px;height:2299px;overflow:hidden}
body{font-family:"Roboto",Arial,sans-serif;color:var(--text);background:var(--white);position:relative}
.abs{position:absolute}

.top-rule{left:0;top:0;width:1200px;height:6px;background:var(--red-bright)}
.site-header{left:0;top:6px;width:1200px;height:115px;background:var(--white)}
.brand{left:100px;top:44px;display:flex;align-items:center;gap:12px}
.brand-dot{width:22px;height:22px;border-radius:50%;background:var(--red-bright)}
.brand-name{font-size:27px;font-weight:500;color:var(--red-bright);letter-spacing:-.3px}
.phone{left:775px;top:44px;display:flex;align-items:center;gap:14px;font-size:22px;color:#555;font-weight:300}
.lang{left:977px;top:33px;width:133px;height:42px;border:1px solid #555;display:flex;align-items:center;justify-content:center;gap:8px;font-size:16px;color:#333}
.flag{width:30px;height:19px}

.main-nav{left:0;top:121px;width:1200px;height:74px;background:linear-gradient(var(--orange-top),var(--orange-bottom))}
.main-nav a{position:absolute;top:0;height:74px;line-height:74px;color:var(--white);text-decoration:none;font-size:15px;text-transform:uppercase}
.main-nav a.active{background:var(--red);width:112px;text-align:center}

.page-title{left:0;top:195px;width:1200px;height:138px;background:var(--dark);color:var(--white);font-size:34px;font-weight:500;display:flex;align-items:center;justify-content:center}

.hero{left:0;top:333px;width:1200px;height:338px}
.hero-map{left:0;top:0;width:1200px;height:338px;background:linear-gradient(135deg,#f5c35a 0%,#f3b84a 45%,#f6c870 100%)}
.hero-title{left:0;top:76px;width:1200px;text-align:center;color:var(--white);font-size:34px;font-weight:500}
.hero-text{left:190px;top:130px;width:800px;text-align:center;color:var(--white);font-size:21px;line-height:31px}
.hero-btn{left:460px;top:222px;width:280px;height:63px;background:var(--white);color:var(--red);font-size:20px;display:flex;align-items:center;justify-content:center;box-shadow:0 2px 4px rgba(0,0,0,.25)}

.band-grey{background:var(--grey-bg)}
.photo-frame{background:var(--white);padding:6px;box-shadow:0 1px 6px rgba(0,0,0,.3)}
.photo{width:100%;height:100%;background:linear-gradient(160deg,var(--photo-light) 0%,var(--photo-dark) 100%)}

.section-title{color:var(--red);font-size:20px;font-weight:400;text-transform:uppercase}
.lead{font-size:13px;line-height:22px;color:var(--text)}
.features{list-style:none}
.features li{font-size:14.5px;color:var(--text);height:31px;display:flex;align-items:center;gap:10px}
.features li::before{content:"»";color:var(--red);font-size:17px;line-height:1}

.data-title{left:0;top:1128px;width:1200px;text-align:center;color:var(--red);font-size:23px;font-weight:400}
.data-table{left:157px;top:1180px;width:886px;border:1px solid #d6d6d6;border-collapse:collapse;box-shadow:0 1px 3px rgba(0,0,0,.1)}
.data-table td{height:44.5px;font-size:15.5px;color:#444;vertical-align:middle}
.data-table td.key{width:255px;padding-left:42px;border-right:2px solid #555}
.data-table td.val{padding-left:52px}
.data-table tr:nth-child(even) td{background:var(--row-alt)}

.price{left:547px;top:1924px;color:var(--red);font-size:18px;font-weight:500}
.order-btn{left:662px;top:1918px;width:114px;height:33px;background:linear-gradient(#f5b235,#e49511);color:var(--white);font-size:12px;font-weight:500;display:flex;align-items:center;justify-content:center;border-radius:2px}

.site-footer{left:0;top:2001px;width:1200px;height:220px;background:var(--footer-red);color:var(--white)}
.foot-head{font-size:15px;font-weight:500;text-transform:uppercase;position:absolute;top:38px}
.foot-links{position:absolute;left:98px;top:78px;list-style:none}
.foot-links li{font-size:12px;height:24.5px}
.foot-links li::before{content:"▸ ";font-size:10px}
.foot-text{position:absolute;font-size:12px;line-height:17.5px}
.newsletter{position:absolute;left:908px;top:114px;display:flex}
.newsletter .field{width:145px;height:30px;background:var(--white);color:#777;font-size:11px;padding-left:14px;display:flex;align-items:center}
.newsletter .send{width:57px;height:30px;background:#e29a1c;color:var(--white);font-size:10px;display:flex;align-items:center;justify-content:center}
.social{position:absolute;top:162px;width:33px;height:33px;border:1px solid rgba(255,255,255,.8);border-radius:50%}

.bottom-bar{left:0;top:2221px;width:1200px;height:78px;background:var(--black);color:var(--white);font-size:11px}
.copyright{position:absolute;left:0;top:31px;width:1200px;text-align:center}
.build-tag{position:absolute;right:22px;top:31px}
</style>
</head>
<body>

<div class="abs top-rule"></div>

<header class="abs site-header">
  <div class="abs brand"><span class="brand-dot"></span><span class="brand-name">GnomonVale.com</span></div>
  <div class="abs phone">
    <svg width="20" height="20" viewBox="0 0 24 24" aria-hidden="true"><path fill="#b71c1c" d="M6.6 10.8a15.1 15.1 0 0 0 6.6 6.6l2.2-2.2a1 1 0 0 1 1-.25 11.4 11.4 0 0 0 3.6.57 1 1 0 0 1 1 1V20a1 1 0 0 1-1 1A17 17 0 0 1 3 4a1 1 0 0 1 1-1h3.5a1 1 0 0 1 1 1c0 1.25.2 2.45.57 3.57a1 1 0 0 1-.25 1z"/></svg>
    (888)555-0147
  </div>
  <div class="abs lang">
    <svg class="flag" viewBox="0 0 30 19" aria-hidden="true">
      <rect width="30" height="19" fill="#fff"/>
      <g fill="#c8102e"><rect y="0" width="30" height="1.5"/><rect y="2.9" width="30" height="1.5"/><rect y="5.8" width="30" height="1.5"/><rect y="8.7" width="30" height="1.5"/><rect y="11.6" width="30" height="1.5"/><rect y="14.5" width="30" height="1.5"/><rect y="17.4" width="30" height="1.6"/></g>
      <rect width="13" height="10.2" fill="#3c3b6e"/>
    </svg>
    English
    <svg width="9" height="6" viewBox="0 0 9 6" aria-hidden="true"><path d="M1 1l3.5 3.5L8 1" stroke="#333" fill="none" stroke-width="1.3"/></svg>
  </div>
</header>

<nav class="abs main-nav">
  <a class="active" style="left:86px">Home</a>
  <a style="left:222px">About us</a>
  <a style="left:355px">Our services</a>
  <a style="left:523px">Products</a>
  <a style="left:667px">Blog</a>
  <a style="left:766px">News</a>
  <a style="left:867px">Location</a>
  <a style="left:1002px">Contact</a>
</nav>

<div class="abs page-title">PRODUCT PAGE</div>

<section class="abs hero">
  <div class="abs hero-map" role="img" aria-label="Faded world map background in warm yellow tones"></div>
  <h1 class="abs hero-title">BUILD YOUR CUSTOMIZED SUNDIAL</h1>
  <p class="abs hero-text">We can manufacture your Sundial, design to your specific location. Becoming a unique piece considering your location, and wall decliantion.</p>
  <div class="abs hero-btn">ORDER YOURS TODAY!</div>
</section>

<section class="abs band-grey" style="left:0;top:671px;width:1200px;height:406px">
  <div class="abs photo-frame" style="left:92px;top:56px;width:431px;height:302px">
    <div class="photo" role="img" aria-label="Photo of a dark wall sundial mounted on a white wall"></div>
  </div>
  <h2 class="abs section-title" style="left:555px;top:70px">Specifications</h2>
  <p class="abs lead" style="left:555px;top:100px;width:560px">Lorem Ipsum has been the industry's standard dummy text ever since the 1500s, when an unknown printer took a galley of type and scrambled it to make a type specimen book</p>
  <ul class="abs features" style="left:555px;top:155px">
    <li>Size 245mm x 345 mm</li>
    <li>Methacrylate board 3mm thick with rounded corners.</li>
    <li>Steeel like cover</li>
    <li>Customized laser engravement with line hours</li>
    <li>Customized Gnomon 3mm black with fitting on board tabs.</li>
    <li>Shipping to EU</li>
  </ul>
</section>

<h2 class="abs data-title">DATA</h2>
<table class="abs data-table">
  <tr><td class="key">Banner:</td><td class="val">Hemisferio sur orientacion Norte</td></tr>
  <tr><td class="key">Longitude:</td><td class="val">-58.209015727</td></tr>
  <tr><td class="key">Latitude:</td><td class="val">-34.7778964567</td></tr>
  <tr><td class="key">Wall declination:</td><td class="val">152.640161591</td></tr>
  <tr><td class="key">Sundial type:</td><td class="val">Wall sundial</td></tr>
  <tr><td class="key">Sundial type:</td><td class="val">Civil Time</td></tr>
  <tr><td class="key">Daylight Saving Time:</td><td class="val">Yes</td></tr>
  <tr><td class="key">Timezone</td><td class="val">(GMT+1)Amsterdam, Berlin, Berne, Rome, Stockholm, Paris, Valencia, Madrid</td></tr>
</table>

<section class="abs band-grey" style="left:0;top:1596px;width:1190px;height:405px">
  <div class="abs photo-frame" style="left:83px;top:55px;width:429px;height:302px">
    <div class="photo" role="img" aria-label="Photo of a dark wall sundial mounted on a white wall"></div>
  </div>
  <h2 class="abs section-title" style="left:545px;top:68px">Buy your customized sundial</h2>
  <p class="abs lead" style="left:545px;top:98px">If you wish we can manufacture your sundial, designed to your specific location</p>
  <ul class="abs features" style="left:545px;top:130px">
    <li>Size 245mm x 345 mm</li>
    <li>Methacrylate board 3mm thick with rounded corners.</li>
    <li>Steeel like cover.</li>
    <li>Customized laser engravement with line hours</li>
    <li>Customized Gnomon 3mm black with fitting on board tabs.</li>
    <li>Shipping to European Union</li>
  </ul>
</section>
<div class="abs price">PRECIO 99€</div>
<div class="abs order-btn">ORDER NOW</div>

<footer class="abs site-footer">
  <h3 class="foot-head" style="left:98px">Links</h3>
  <ul class="foot-links">
    <li>Customer Support</li>
    <li>Documentation</li>
    <li>Resources</li>
    <li>General FAQs</li>
    <li>Shortcodes</li>
  </ul>
  <h3 class="foot-head" style="left:311px">Neque porro quisquam</h3>
  <p class="foot-text" style="left:311px;top:77px;width:252px">Lorem Ipsum has been the industry's standard dummy text ever since the 1500s, when an unknown printer took a galley of type and scrambled it to make a type specimen book. It has survived not only five centuries, but also the leap into electronic typesetting, remaining</p>
  <h3 class="foot-head" style="left:650px">Get in touch</h3>
  <p class="foot-text" style="left:650px;top:79px;width:210px;line-height:22px">Address : 220 Larkspur Lane, Brenford, Ontario K4R1T8</p>
  <p class="foot-text" style="left:650px;top:132px">Phone : 1 844 555-0193</p>
  <p class="foot-text" style="left:650px;top:157px">Email : hello@gnomonvale.com</p>
  <h3 class="foot-head" style="left:908px">Newsletter</h3>
  <p class="foot-text" style="left:908px;top:75px;width:205px">Your about us information would fit here nicely.</p>
  <div class="newsletter"><div class="field">Email address</div><div class="send">Submit</div></div>
  <span class="social" style="left:908px"></span>
  <span class="social" style="left:956px"></span>
  <span class="social" style="left:1004px"></span>
</footer>

<div class="abs bottom-bar">
  <p class="copyright">Copyright © 2016. All Rights Reserved</p>
  <span class="build-tag">C6</span>
</div>

</body>
</html>
```